Bramblewick Forage Business Cards

I need a business card with my logo, number, Facebook account, and some information about what I am selling. Green card with logo on the front. 555-214-8392 phone number, @bramblewickforage Facebook, •Orchardgrass Hay •Alfalfa Hay •Mixed Grass Hay , and “Premium Quality Hay” all written on the back.

Target Market(s)

Hay

Contact Information for Business Card

Phone number, Facebook, different types of hay.

Colors
00AB8E
00BBA5
67D7C9
C6EFE9
E9F9F6

```html
<!DOCTYPE html>
<html lang="en">
<head>
<meta charset="utf-8">
<title>Bramblewick Forage Business Cards</title>
<link href="https://fonts.googleapis.com/css2?family=Arimo:wght@400;700&display=swap" rel="stylesheet">
<style>
  :root {
    --backdrop: #e6e3de;
    --card-dark: #050708;
    --card-light: #ffffff;
    --brand-green: #00a651;
    --text-light: #ffffff;
    --text-dark: #111111;
    --text-muted: #d6d6d6;
    --divider: #b5b5b5;
  }
  * { box-sizing: border-box; margin: 0; padding: 0; }
  html, body { width: 1200px; height: 900px; overflow: hidden; }
  body {
    background: var(--backdrop);
    font-family: "Arimo", Arial, sans-serif;
    display: flex;
    flex-direction: column;
    align-items: center;
    justify-content: center;
    gap: 40px;
  }
  .card {
    position: relative;
    width: 700px;
    height: 400px;
    overflow: hidden;
    box-shadow: 0 6px 18px rgba(0,0,0,.25);
  }
  /* Front */
  .card-front {
    background: var(--card-dark);
    display: flex;
    align-items: center;
    justify-content: center;
    gap: 26px;
  }
  .brand-dot {
    width: 96px; height: 96px;
    border-radius: 50%;
    background: var(--brand-green);
    flex: none;
  }
  .front-text { color: var(--text-light); }
  .front-name {
    font-size: 38px;
    font-weight: 700;
    line-height: 1.1;
  }
  .front-phone {
    font-size: 40px;
    font-weight: 700;
    margin-top: 8px;
    letter-spacing: 1px;
  }
  /* Back */
  .card-back { background: var(--card-light); }
  .back-swoosh { position: absolute; inset: 0; }
  .back-brand {
    position: absolute;
    top: 62px; left: 150px;
    display: flex;
    align-items: center;
  }
  .back-brand .brand-dot { width: 78px; height: 78px; }
  .back-divider {
    width: 1px; height: 90px;
    background: var(--divider);
    margin: 0 26px 0 44px;
  }
  .back-name {
    font-size: 36px;
    font-weight: 700;
    color: var(--text-dark);
  }
  .contact-list {
    position: absolute;
    top: 205px; left: 70px;
    list-style: none;
    display: flex;
    flex-direction: column;
    gap: 14px;
  }
  .contact-item {
    display: flex;
    align-items: center;
    gap: 14px;
    font-size: 19px;
    color: var(--text-dark);
  }
  .contact-icon {
    width: 32px; height: 32px;
    border-radius: 50%;
    background: var(--brand-green);
    display: flex; align-items: center; justify-content: center;
    flex: none;
  }
  .hay-list {
    position: absolute;
    right: 36px; bottom: 40px;
    text-align: right;
    color: var(--text-muted);
    font-size: 17px;
    line-height: 1.7;
  }
  .hay-list .dot {
    display: inline-block;
    width: 9px; height: 9px;
    border-radius: 50%;
    background: var(--brand-green);
    margin: 0 8px;
    vertical-align: middle;
  }
</style>
</head>
<body>
  <section class="card card-front">
    <span class="brand-dot"></span>
    <div class="front-text">
      <p class="front-name">Bramblewick Forage</p>
      <p class="front-phone">555-214-8392</p>
    </div>
  </section>

  <section class="card card-back">
    <svg class="back-swoosh" width="700" height="400" viewBox="0 0 700 400" aria-hidden="true">
      <path d="M0,318 C260,322 440,250 580,160 C460,262 280,338 0,338 Z" fill="var(--brand-green)"/>
      <path d="M0,348 C290,348 470,260 700,140 L700,400 L0,400 Z" fill="var(--card-dark)"/>
    </svg>

    <div class="back-brand">
      <span class="brand-dot"></span>
      <span class="back-divider"></span>
      <span class="back-name">Bramblewick Forage</span>
    </div>

    <ul class="contact-list">
      <li class="contact-item">
        <span class="contact-icon">
          <svg width="18" height="18" viewBox="0 0 24 24" aria-hidden="true">
            <path d="M6.6 10.8a15.1 15.1 0 0 0 6.6 6.6l2.2-2.2a1 1 0 0 1 1-.25 11.4 11.4 0 0 0 3.6.57 1 1 0 0 1 1 1V20a1 1 0 0 1-1 1A17 17 0 0 1 3 4a1 1 0 0 1 1-1h3.5a1 1 0 0 1 1 1c0 1.25.2 2.45.57 3.6a1 1 0 0 1-.25 1z" fill="#fff"/>
          </svg>
        </span>
        555-214-8392
      </li>
      <li class="contact-item">
        <span class="contact-icon"></span>
        @bramblewickforage
      </li>
    </ul>

    <div class="hay-list">
      <p>Orchardgrass Hay<span class="dot"></span>Alfalfa Hay<span class="dot"></span></p>
      <p>Mixed Grass Hay<span class="dot"></span>Premium Quality Hay<span class="dot"></span></p>
    </div>
  </section>
</body>
</html>
```